Moxy Fen needs some awesome stationary

Do you have what it takes to get my brand? You either do or you don't, have a crack at a design and you my just win my business.

I don't want to waste your or my time, so put your creative genius on either a business card or envelope.

I however need a package of stationary that follows the same brand. I will message you to complete the remaining should I like your first submission.

Here is what I need, have a go!

Basically I need the following for my small business based in melbourne.
- Letterhead (printer ready and MS Word)
- Business Card
- Compliments Slip
- Envelope
- Proposal Cover Page (MS Word only)
- Presentation Folder
- Marbled Fox Cards
- Student Name Tent
- Index Cards
- Vell-Ka

I am establishing the brand and it must be modern, professional but also relaxed; that is not formal and not corporate. It represents a company are leaders, but small enough to care and operate like a bunch of friends. We are bringing people and conversations back to business, and turfing out all the bureaucracy and crazy and wasteful procedures. Its about "lets talk and figure it out together and find even better ways".

Target Market(s)

Mainly companies that build software products, but Agile practices are used in many other industries (even graphic design projects)

Industry/Entity Type

Information Technology

Font styles to use
Sans Serif

Colors
3176b5
aaaaaa

Requirements
Must have
• I like curves and circles and not boxes or rectangles.
• I want a colour rich design with my brand colours, but it must be balanced.
• I want more modern than traditional, but simple modern
Should not have
• Not corporate
• Please don't waste my time if your not going to think about it.
• Don't mess with my primary logo
• Don't change my colours
• Don't overlay logo on image

```html
<!DOCTYPE html>
<html lang="en">
<head>
<meta charset="utf-8">
<title>Moxy Fen Business Card</title>
<link rel="stylesheet" href="https://fonts.googleapis.com/css2?family=Source+Sans+3:wght@400;600&display=swap">
<style>
  :root {
    --page-bg: #e9eaec;
    --card-bg: #f7f8fa;
    --card-edge: #d4d8de;
    --brand-navy: #2b4585;
    --band-dark: #1f3674;
    --band-mid: #2d4b93;
    --band-light: #3e5d9f;
    --brand-grey: #aaaaaa;
    --text-dark: #3a3d44;
    --text-white: #ffffff;
    --text-soft: #dfe6f5;
  }
  * { margin: 0; padding: 0; box-sizing: border-box; }
  html, body {
    width: 1200px; height: 969px; overflow: hidden;
    background: var(--page-bg);
    font-family: "Source Sans 3", "Helvetica Neue", Arial, sans-serif;
  }
  .business-card {
    position: absolute; left: 100px; top: 200px;
    width: 1000px; height: 568px;
    background: var(--card-bg);
    border: 2px solid var(--card-edge);
    border-radius: 34px;
    overflow: hidden;
    box-shadow: 0 10px 30px rgba(0,0,0,0.12);
  }
  .brand-mark {
    position: absolute; left: 78px; top: 50px;
    width: 160px; height: 160px; border-radius: 50%;
    background: var(--brand-navy);
  }
  .brand-name {
    position: absolute; left: 72px; top: 205px;
    font-size: 50px; font-weight: 600; color: var(--brand-navy);
    letter-spacing: 0.5px;
  }
  .name-band {
    position: absolute; left: 0; top: 280px; width: 100%; height: 90px;
    background: linear-gradient(90deg, var(--band-dark) 0%, var(--band-mid) 55%, var(--band-light) 100%);
  }
  .person-name {
    position: absolute; left: 56px; top: 6px;
    font-size: 35px; font-weight: 600; color: var(--text-white);
  }
  .person-title {
    position: absolute; left: 56px; top: 48px;
    font-size: 26px; font-weight: 400; color: var(--text-soft);
  }
  .band-circle {
    position: absolute; left: 725px; top: -12px;
    width: 114px; height: 114px; border-radius: 50%;
    border: 4px solid rgba(255,255,255,0.75);
    background: rgba(255,255,255,0.12);
  }
  .contact-list {
    position: absolute; left: 54px; top: 392px; list-style: none;
  }
  .contact-list li {
    display: flex; align-items: center; gap: 14px;
    height: 38px; font-size: 25px; color: var(--text-dark);
  }
  .contact-list svg { width: 24px; height: 24px; fill: var(--brand-navy); flex: none; }
  .postal-address {
    position: absolute; right: 58px; top: 430px;
    text-align: right; font-style: normal;
    font-size: 25px; line-height: 38px; color: var(--text-dark);
  }
</style>
</head>
<body>
  <div class="business-card">
    <div class="brand-mark"></div>
    <div class="brand-name">Moxy Fen</div>

    <div class="name-band">
      <div class="person-name">Dara Quillon</div>
      <div class="person-title">CEO, Professional Scrum Trainer</div>
      <div class="band-circle"></div>
    </div>

    <ul class="contact-list">
      <li>
        <svg viewBox="0 0 24 24" aria-hidden="true"><path d="M6.6 10.8a15 15 0 0 0 6.6 6.6l2.2-2.2a1 1 0 0 1 1-.25 11.4 11.4 0 0 0 3.6.6 1 1 0 0 1 1 1V20a1 1 0 0 1-1 1A17 17 0 0 1 3 4a1 1 0 0 1 1-1h3.5a1 1 0 0 1 1 1c0 1.25.2 2.45.6 3.6a1 1 0 0 1-.25 1z"/></svg>
        1300MOXYF
      </li>
      <li>
        <svg viewBox="0 0 24 24" aria-hidden="true"><path d="M7 1h10a2 2 0 0 1 2 2v18a2 2 0 0 1-2 2H7a2 2 0 0 1-2-2V3a2 2 0 0 1 2-2zm0 3v14h10V4zm5 15.5a1.2 1.2 0 1 0 0 2.4 1.2 1.2 0 0 0 0-2.4z"/></svg>
        +61 400 218 736
      </li>
      <li>
        <svg viewBox="0 0 24 24" aria-hidden="true"><path d="M2 5h20v14H2zm2 2v.5l8 5 8-5V7zm0 2.8V17h16V9.8l-8 5z"/></svg>
        dara@moxy-fen.com.au
      </li>
      <li>
        <svg viewBox="0 0 24 24" aria-hidden="true"><path d="M12 2a10 10 0 1 0 0 20 10 10 0 0 0 0-20zm-1 17.9A8 8 0 0 1 4.1 11H7c.1 3 1.4 6 4 8.9zM13 19.9c2.6-2.9 3.9-5.9 4-8.9h2.9a8 8 0 0 1-6.9 8.9zM9 11h6c-.1 2.6-1.1 5-3 7.3-1.9-2.3-2.9-4.7-3-7.3zm-4.9-2A8 8 0 0 1 11 4.1C8.4 7 7.1 8 7 9zm4.9 0c.1-1 1.1-2.6 3-4.3 1.9 1.7 2.9 3.3 3 4.3zm8 0c-.1-1-1.4-2-4-4.9A8 8 0 0 1 19.9 9z"/></svg>
        www.moxy-fen.com.au
      </li>
    </ul>

    <address class="postal-address">
      PO Box 4817<br>
      Ashbrook Vale<br>
      VIC 3199, Australia
    </address>
  </div>
</body>
</html>
```